Maplecrest Disability - Social Security Disability Attorneys

Our company is expanding to attract clients nationwide for our social security disability practice. We have a logo, but I am looking for a creative and elegant letterhead that projects an image of being technologically advanced but still professional enough for the legal field. I am looking for the "wow factor" combined with this is still professional enough for a law practice.

Requesting letterhead and business card design
Updates

Had to update and change the logo. The previous logo had a typo. Please send updates with the new logo for consideration. The letterhead and business cards should be professional enough to be used for a law firm. Thanks.

Industry/Entity Type

Law Practice, Law Firm, Healthcare Industry, Government

Colors

Designer to choose colors to be used in the design.

Requirements
Nice to have
• **Please create a vertical design for the business card**

```html
<!DOCTYPE html>
<html lang="en">
<head>
<meta charset="utf-8">
<title>Maplecrest Disability Letterhead</title>
<link href="https://fonts.googleapis.com/css2?family=Lato:wght@400;700&family=Montserrat:wght@400;500&family=Allura&display=swap" rel="stylesheet">
<style>
  :root {
    --backdrop: #dedede;
    --paper: #ffffff;
    --brand-blue: #3f5fd8;
    --band-blue: #546fb8;
    --accent-orange: #f7852b;
    --ink: #2b2b2b;
    --ink-soft: #3a3a3a;
  }
  * { margin: 0; padding: 0; box-sizing: border-box; }
  html, body {
    width: 1200px; height: 800px; overflow: hidden;
    background: var(--backdrop);
  }
  .stage { position: relative; width: 1200px; height: 800px; }
  .sheet {
    position: absolute; top: 111px;
    width: 413px; height: 575px;
    background: var(--paper);
    overflow: hidden;
  }
  .sheet--letter { left: 165px; }
  .sheet--blank { left: 611px; }

  .brand {
    position: absolute; left: 23px; top: 49px;
    display: flex; flex-direction: column; align-items: center;
  }
  .brand__row { display: flex; align-items: center; gap: 4px; }
  .brand__dot {
    width: 7px; height: 7px; border-radius: 50%;
    background: var(--accent-orange);
  }
  .brand__name {
    font-family: 'Lato', sans-serif; font-weight: 700;
    font-size: 11.5px; letter-spacing: 1.3px; text-transform: uppercase;
    color: var(--brand-blue);
  }
  .brand__tagline {
    margin-top: 2px;
    font-family: 'Lato', sans-serif; font-weight: 400;
    font-size: 3.3px; letter-spacing: 0.9px; text-transform: uppercase;
    color: var(--brand-blue);
  }

  .contact {
    position: absolute; left: 292px; top: 32px;
    border-left: 1px solid var(--accent-orange);
    padding-left: 6px;
    font-family: 'Montserrat', sans-serif; font-size: 6.4px;
    color: var(--ink); line-height: 9.6px;
  }
  .contact__address { margin-bottom: 2px; }
  .contact__item { display: flex; align-items: center; gap: 4px; }
  .contact__icon { width: 6px; height: 6px; flex: none; }

  .letter {
    position: absolute; left: 23px; top: 118px; width: 368px;
    font-family: 'Lato', sans-serif; font-size: 8px; color: var(--ink-soft);
    line-height: 9.5px;
  }
  .letter__date { font-size: 8.4px; margin-bottom: 10px; }
  .letter__block { margin-bottom: 9px; }
  .letter__salutation {
    font-weight: 700; font-size: 10px; color: var(--ink);
    margin: 14px 0 11px;
  }
  .letter__para {
    text-align: justify; line-height: 9px; margin-bottom: 9px;
  }
  .letter__closing { margin-top: 19px; }
  .letter__signature {
    font-family: 'Allura', cursive; font-size: 22px; color: var(--ink);
    margin-top: 12px; line-height: 22px;
  }

  .wave {
    position: absolute; left: 0; bottom: 0;
    width: 413px; height: 80px; display: block;
  }
  .wave__band { fill: var(--band-blue); }
  .wave__ribbon { fill: var(--accent-orange); }
</style>
</head>
<body>
<main class="stage">

  <article class="sheet sheet--letter">
    <header>
      <div class="brand">
        <div class="brand__row"><span class="brand__dot"></span><span class="brand__name">Maplecrest Disability</span></div>
        <span class="brand__tagline">Social Security Disability Attorneys</span>
      </div>
      <address class="contact" style="font-style:normal">
        <div class="contact__address">Suite 5, Level 18, Wattle<br>Street Sydney NSW 2010</div>
        <div class="contact__item">
          <svg class="contact__icon" viewBox="0 0 10 10"><path d="M2 1 L4 1 L4.6 3.2 L3.4 4 Q4.5 6 6 6.6 L6.8 5.4 L9 6 L9 8 Q9 9 8 9 Q1 8.6 1 2 Q1 1 2 1Z" fill="var(--accent-orange)"/></svg>
          <span>555-210-4417</span>
        </div>
        <div class="contact__item">
          <svg class="contact__icon" viewBox="0 0 10 10"><rect x="0.5" y="2" width="9" height="6.5" fill="var(--accent-orange)"/><path d="M0.5 2 L5 5.6 L9.5 2" fill="none" stroke="#fff" stroke-width="0.9"/></svg>
          <span>info@maplecrestdisability.com</span>
        </div>
        <div class="contact__item">
          <svg class="contact__icon" viewBox="0 0 10 10"><circle cx="5" cy="5" r="4.5" fill="var(--accent-orange)"/><path d="M0.5 5 H9.5 M5 0.5 Q2.5 5 5 9.5 M5 0.5 Q7.5 5 5 9.5" fill="none" stroke="#fff" stroke-width="0.6"/></svg>
          <span>www.maplecrestdisability.com</span>
        </div>
      </address>
    </header>

    <section class="letter">
      <p class="letter__date">January-03-2020</p>
      <p class="letter__block">Mr, James Carter<br>President</p>
      <p class="letter__block">Bridgeway Corporation<br>123 Street Name, Suite# 10<br>City, State, 120023</p>
      <p class="letter__salutation">Dear Mr, James</p>
      <p class="letter__para">Lorem ipsum dolor sit amet, consectetur adipisicing elit, sed do eiusmod tempor incididunt ut labore et dolore magna aliqua. Ut enim ad minim veniam, quis nostrud exercitation ullamco laboris nisi ut aliquip ex ea commodo consequat. Duis aute irure dolor in reprehenderit in voluptate velit esse cillum dolore eu fugiat nulla pariatur.</p>
      <p class="letter__para">Lorem ipsum dolor sit amet, consectetur adipisicing elit, sed do eiusmod tempor incididunt ut labore et dolore magna aliqua. Ut enim ad minim veniam, quis nostrud exercitation ullamco laboris nisi ut aliquip ex ea commodo consequat. Duis aute irure dolor in reprehenderit in voluptate velit esse cillum dolore eu fugiat nulla pariatur.</p>
      <p class="letter__para">Lorem ipsum dolor sit amet, consectetur adipisicing elit, sed do eiusmod tempor incididunt ut labore et dolore magna aliqua. Ut enim ad minim veniam, quis nostrud exercitation ullamco laboris nisi ut aliquip ex ea commodo consequat.</p>
      <p class="letter__para">Excepteur sint occaecat cupidatat non proident, sunt in culpa qui officia deserunt mollit anim id est laborum. re et dolore magnam aliquam quaerat voluptatem.</p>
      <p class="letter__closing">Regards</p>
      <p class="letter__signature">Daniel Hayes</p>
    </section>

    <svg class="wave" viewBox="0 970 810 156" preserveAspectRatio="none">
      <path class="wave__band" d="M0,975 C120,1045 200,1052 300,1048 C420,1042 520,1018 600,1018 C680,1018 740,1030 810,1060 L810,1126 L0,1126 Z"/>
      <path class="wave__ribbon" d="M57,1000 C120,1030 190,1038 260,1036 C400,1032 500,1002 590,1002 C660,1002 720,1015 754,1032 C710,1020 660,1012 590,1012 C500,1012 400,1042 260,1044 C180,1045 110,1030 57,1000 Z"/>
    </svg>
  </article>

  <article class="sheet sheet--blank">
    <header>
      <div class="brand">
        <div class="brand__row"><span class="brand__dot"></span><span class="brand__name">Maplecrest Disability</span></div>
        <span class="brand__tagline">Social Security Disability Attorneys</span>
      </div>
      <address class="contact" style="font-style:normal">
        <div class="contact__address">Suite 5, Level 18, Wattle<br>Street Sydney NSW 2010</div>
        <div class="contact__item">
          <svg class="contact__icon" viewBox="0 0 10 10"><path d="M2 1 L4 1 L4.6 3.2 L3.4 4 Q4.5 6 6 6.6 L6.8 5.4 L9 6 L9 8 Q9 9 8 9 Q1 8.6 1 2 Q1 1 2 1Z" fill="var(--accent-orange)"/></svg>
          <span>555-210-4417</span>
        </div>
        <div class="contact__item">
          <svg class="contact__icon" viewBox="0 0 10 10"><rect x="0.5" y="2" width="9" height="6.5" fill="var(--accent-orange)"/><path d="M0.5 2 L5 5.6 L9.5 2" fill="none" stroke="#fff" stroke-width="0.9"/></svg>
          <span>info@maplecrestdisability.com</span>
        </div>
        <div class="contact__item">
          <svg class="contact__icon" viewBox="0 0 10 10"><circle cx="5" cy="5" r="4.5" fill="var(--accent-orange)"/><path d="M0.5 5 H9.5 M5 0.5 Q2.5 5 5 9.5 M5 0.5 Q7.5 5 5 9.5" fill="none" stroke="#fff" stroke-width="0.6"/></svg>
          <span>www.maplecrestdisability.com</span>
        </div>
      </address>
    </header>

    <svg class="wave" viewBox="0 970 810 156" preserveAspectRatio="none">
      <path class="wave__band" d="M0,975 C120,1045 200,1052 300,1048 C420,1042 520,1018 600,1018 C680,1018 740,1030 810,1060 L810,1126 L0,1126 Z"/>
      <path class="wave__ribbon" d="M57,1000 C120,1030 190,1038 260,1036 C400,1032 500,1002 590,1002 C660,1002 720,1015 754,1032 C710,1020 660,1012 590,1012 C500,1012 400,1042 260,1044 C180,1045 110,1030 57,1000 Z"/>
    </svg>
  </article>

</main>
</body>
</html>
```